Request for Business Card Design

Hi. My name is Marlene, I am looking for a new business card design for my company, Quarrow Signal Instruments, LLC. I really like the design you did for Tarsel Venture and was hoping you could do something similar using our full logo and our mark. I am also open to any raised texture design using our mark. I have attached our full logo, which would need to be somewhere on the card, as well as the mark in both outline and full form, as well as our brand colors / guide. The card does not have to be white, as long as our logo and mark appear. I actually like darker colored business cards more, but am open to all options. If you are interested in working with me, please let me know. We would also take the business card design into letterhead design if you can do that.

```html
<!DOCTYPE html>
<html lang="en">
<head>
<meta charset="utf-8">
<title>Quarrow Signal Instruments – Business Card</title>
<link rel="stylesheet" href="https://fonts.googleapis.com/css2?family=Open+Sans:wght@400;600;800&display=swap">
<style>
  :root {
    --backdrop: #222223;
    --card: #3f3f41;
    --ink-dark: #19191a;
    --accent: #1f9fd1;
    --text-light: #f4f4f4;
  }
  * { margin: 0; padding: 0; box-sizing: border-box; }
  html, body {
    width: 1200px; height: 780px; overflow: hidden;
    background: var(--backdrop);
    font-family: "Open Sans", Arial, sans-serif;
  }
  .canvas { position: relative; width: 1200px; height: 780px; }
  .card {
    position: absolute;
    width: 560px; height: 320px;
    background: var(--card);
    border-radius: 3px;
    overflow: hidden;
  }
  .card--front { left: 320px; top: 50px; }
  .card--back  { left: 320px; top: 410px; }

  /* Front */
  .front-brand {
    position: absolute; inset: 0;
    display: flex; align-items: center; justify-content: center; gap: 16px;
  }
  .brand-dot {
    flex: none;
    width: 46px; height: 46px; border-radius: 50%;
    background: var(--ink-dark);
  }
  .brand-name {
    color: var(--ink-dark);
    font-weight: 800;
    font-size: 30px;
    line-height: 1.05;
    letter-spacing: 1px;
    text-transform: uppercase;
    white-space: nowrap;
  }

  /* Back: brand runs upward along the left edge */
  .back-brand {
    position: absolute;
    left: 26px; bottom: 26px;
    transform-origin: left bottom;
    transform: rotate(-90deg) translateY(100%);
    display: flex; align-items: center; gap: 12px;
  }
  .back-brand .brand-dot { width: 36px; height: 36px; }
  .back-brand .brand-name { font-size: 18px; line-height: 1.1; }

  .contact {
    position: absolute; right: 40px; top: 52px;
    text-align: right; color: var(--text-light);
  }
  .contact__name {
    color: var(--accent); font-weight: 800; font-size: 34px; line-height: 1;
  }
  .contact__role { font-weight: 600; font-size: 14px; margin-top: 2px; }
  .accent-bar {
    position: absolute; right: 0; top: 52px;
    width: 26px; height: 40px; background: var(--accent);
  }
  .contact__address { font-size: 13px; line-height: 1.4; margin-top: 20px; }
  .contact__lines { list-style: none; margin-top: 16px; font-size: 13px; line-height: 1.55; }
  .contact__lines li { display: flex; justify-content: flex-end; align-items: center; gap: 8px; }
  .icon { width: 13px; height: 13px; fill: none; stroke: var(--accent); stroke-width: 2; }
</style>
</head>
<body>
<main class="canvas">
  <section class="card card--front" aria-label="Card front">
    <div class="front-brand">
      <span class="brand-dot"></span>
      <span class="brand-name">Quarrow Signal<br>Instruments</span>
    </div>
  </section>

  <section class="card card--back" aria-label="Card back">
    <div class="back-brand">
      <span class="brand-dot"></span>
      <span class="brand-name">Quarrow Signal<br>Instruments</span>
    </div>

    <span class="accent-bar"></span>
    <div class="contact">
      <p class="contact__name">Marlene</p>
      <p class="contact__role">Director</p>
      <p class="contact__address">1180 Larkspur Commons Way •<br>Fenwick, CO 80721</p>
      <ul class="contact__lines">
        <li>+001 555 218 4407
          <svg class="icon" viewBox="0 0 16 16"><path d="M3 2l3 0 1 3-2 1.5a8 8 0 0 0 4.5 4.5L11 9l3 1v3a1 1 0 0 1-1 1A12 12 0 0 1 2 3a1 1 0 0 1 1-1z"/></svg></li>
        <li>+001 555 218 4490
          <svg class="icon" viewBox="0 0 16 16"><rect x="2" y="6" width="12" height="8"/><rect x="5" y="2" width="6" height="4"/></svg></li>
        <li>www.quarrowsignal.com
          <svg class="icon" viewBox="0 0 16 16"><circle cx="8" cy="8" r="6"/><path d="M2 8h12M8 2c3 3 3 9 0 12M8 2c-3 3-3 9 0 12"/></svg></li>
        <li>info@quarrowsignal.com
          <svg class="icon" viewBox="0 0 16 16"><rect x="2" y="4" width="12" height="9"/><path d="M2 4l6 5 6-5"/></svg></li>
      </ul>
    </div>
  </section>
</main>
</body>
</html>
```